New Business Cards for Tormin Group

We need a new Business Card to compliment our new logo. We are a vibrant design, manufacture and install business providing recreation areas, public parks and Municipal spaces. We want business cards that are classy, modern and clean.

We have recently changed our logo, and are celebrating our 40th anniversary. We want business cards with a new modern design to reflect our status.

Target Market(s)

Customers

Contact Information for Business Card

We need all the details of our 3 offices as per the business card attached. Please disregard the old logo on the business card, the other three files show our new logo.

Requirements
Must have
• All info as per attached business card but with new logo.
Nice to have

```html
<!DOCTYPE html>
<html lang="en">
<head>
<meta charset="UTF-8">
<title>Tormin Group – Business Cards</title>
<link href="https://fonts.googleapis.com/css2?family=Work+Sans:wght@400;500;600&display=swap" rel="stylesheet">
<style>
  :root{
    --stage:#161616;
    --card:#232323;
    --ink:#f2f2f2;
    --accent:#e8303a;
    --silver:#8e8e8e;
  }
  *{margin:0;padding:0;box-sizing:border-box}
  html,body{width:1200px;height:900px;overflow:hidden;background:var(--stage)}
  body{font-family:"Work Sans",sans-serif;color:var(--ink);position:relative}
  .card{position:absolute;left:250px;width:700px;height:400px;background:var(--card);border-radius:3px;box-shadow:0 10px 30px rgba(0,0,0,.6)}
  .card--offices{top:35px}
  .card--profile{top:465px}

  .brand{display:flex;align-items:center;gap:12px;position:absolute}
  .brand__mark{border-radius:50%;flex:none}
  .brand__name{font-weight:600;white-space:nowrap}
  .card--offices .brand{left:50px;top:40px}
  .card--offices .brand__mark{width:58px;height:58px;background:#2e2e2e}
  .card--offices .brand__name{font-size:30px;color:var(--silver)}

  .offices{position:absolute;left:50px;right:24px;top:150px;display:flex;gap:22px}
  .office{flex:1;font-size:13px;line-height:1.55;white-space:nowrap}
  .office__title{color:var(--accent);font-size:19px;font-weight:500;margin-bottom:4px}
  .office__address{margin-bottom:12px}
  .office__label{color:var(--accent)}

  .card--profile .brand{left:50px;top:165px}
  .card--profile .brand__mark{width:68px;height:68px;background:var(--accent)}
  .card--profile .brand__name{font-size:30px;color:var(--ink)}
  .divider{position:absolute;left:372px;top:95px;width:2px;height:150px;background:var(--accent)}

  .person{position:absolute;left:405px;top:110px}
  .person__name{color:var(--accent);font-size:25px;font-weight:500;letter-spacing:1px;text-transform:uppercase;white-space:nowrap}
  .person__role{font-size:18px;margin-bottom:18px}
  .contacts{list-style:none;font-size:18px;line-height:1.55;white-space:nowrap}
  .contacts li{display:flex;align-items:center;gap:12px}
  .contacts svg{width:14px;height:14px;flex:none}
</style>
</head>
<body>

<section class="card card--offices">
  <div class="brand">
    <span class="brand__mark"></span>
    <span class="brand__name">Tormin Group</span>
  </div>
  <div class="offices">
    <div class="office">
      <h3 class="office__title">Head Office</h3>
      <p class="office__address">P.O. Box:<br>48210 Abu Dhabi, U.A.E.</p>
      <p><span class="office__label">P</span> : +971 (0)2 5500412</p>
      <p><span class="office__label">F</span> : +971 (0)2 5500413</p>
      <p><span class="office__label">E</span> : sales@tormingroup.com</p>
    </div>
    <div class="office">
      <h3 class="office__title">Dubai Office</h3>
      <p class="office__address">P. O. Box:<br>271846 Dubai, U.A.E.</p>
      <p><span class="office__label">P</span> : +971 (0)4 3307725</p>
      <p><span class="office__label">F</span> : +971 (0)4 3307726</p>
      <p><span class="office__label">E</span> : sales@tormingroup.com</p>
    </div>
    <div class="office">
      <h3 class="office__title">Qatar Office</h3>
      <p class="office__address">P. O. Box:<br>30927 Doha, Qatar</p>
      <p><span class="office__label">P</span> : +974 44718830</p>
      <p><span class="office__label">F</span> : +974 44718831</p>
      <p><span class="office__label">E</span> : sales@tormingroup.com</p>
    </div>
  </div>
</section>

<section class="card card--profile">
  <div class="brand">
    <span class="brand__mark"></span>
    <span class="brand__name">Tormin Group</span>
  </div>
  <span class="divider"></span>
  <div class="person">
    <h2 class="person__name">Elias Marrow</h2>
    <p class="person__role">Managing Partner</p>
    <ul class="contacts">
      <li>
        <svg viewBox="0 0 16 16" aria-hidden="true"><path d="M4 1l3 3-2 2c1 2 3 4 5 5l2-2 3 3-2 2C7 14 2 9 2 3z" fill="var(--accent)"/></svg>
        +971 (0)50 384 9017
      </li>
      <li>
        <svg viewBox="0 0 16 16" aria-hidden="true"><rect x="1.5" y="3.5" width="13" height="9" fill="none" stroke="var(--accent)" stroke-width="1.4"/><path d="M1.5 3.5l6.5 5 6.5-5" fill="none" stroke="var(--accent)" stroke-width="1.4"/></svg>
        elias@tormingroup.com
      </li>
      <li>
        <svg viewBox="0 0 16 16" aria-hidden="true"><g fill="none" stroke="var(--accent)" stroke-width="1.3"><circle cx="8" cy="8" r="6.5"/><ellipse cx="8" cy="8" rx="3" ry="6.5"/><path d="M1.5 8h13M2.5 4.8h11M2.5 11.2h11"/></g></svg>
        www.tormingroup.com
      </li>
    </ul>
  </div>
</section>

</body>
</html>
```